BRIGHTWAY MOTOR SALES
BRIGHTWAY MOTOR SALES -
Creative Brief
Professional
DARYL FENN
SALES REP
472 N.CORBIN AVE LARKMOOR VALE 45990
BRIGHTWAYMOTORSALES@EXAMPLEMAIL.COM
WWW.CRESTVALEMOTORCARS.EXAMPLE

```html
<!DOCTYPE html>
<html lang="en">
<head>
<meta charset="utf-8">
<title>Brightway Motor Sales – Business Card</title>
<link rel="stylesheet" href="https://fonts.googleapis.com/css2?family=Source+Sans+3:wght@400;600;700&display=swap">
<style>
  :root {
    --backdrop: #d9d9d9;
    --card: #ffffff;
    --magenta: #c2197f;
    --magenta-light: #e04aa5;
    --green: #7cc242;
    --text: #555555;
    --divider: #d6d6d6;
  }
  * { margin: 0; padding: 0; box-sizing: border-box; }
  html, body {
    width: 1200px; height: 780px; overflow: hidden;
    background: var(--backdrop);
    font-family: "Source Sans 3", "Myriad Pro", Arial, sans-serif;
  }
  .business-card {
    position: absolute; left: 100px; top: 100px;
    width: 1000px; height: 580px;
    background: var(--card);
    border-radius: 28px;
    overflow: hidden;
    box-shadow: 0 8px 24px rgba(0,0,0,0.18);
  }
  .corner-swoosh { position: absolute; left: 0; top: 0; width: 1000px; height: 580px; }
  .brand {
    position: absolute; left: 40px; top: 255px; width: 340px;
    display: flex; align-items: center; gap: 14px;
  }
  .brand-dot { width: 34px; height: 34px; border-radius: 50%; background: var(--magenta); flex: none; }
  .brand-name {
    font-size: 34px; font-weight: 700; line-height: 1.05;
    color: var(--magenta); letter-spacing: 0.5px;
  }
  .divider {
    position: absolute; left: 420px; top: 70px; width: 2px; height: 420px;
    background: var(--divider);
  }
  .contact { position: absolute; left: 455px; top: 70px; color: var(--text); }
  .contact-name { font-size: 46px; font-weight: 700; color: var(--magenta); line-height: 1; }
  .contact-role { font-size: 24px; font-weight: 600; color: var(--green); margin-top: 6px; }
  .contact-address { font-size: 24px; line-height: 1.3; margin-top: 56px; }
  .contact-list { list-style: none; margin-top: 52px; }
  .contact-list li {
    display: flex; align-items: center; gap: 14px;
    font-size: 24px; line-height: 1; height: 40px;
  }
  .contact-list svg { width: 22px; height: 22px; flex: none; fill: var(--magenta); }
</style>
</head>
<body>
  <div class="business-card">
    <svg class="corner-swoosh" viewBox="0 0 1000 580" aria-hidden="true">
      <path d="M0 230 C 40 330, 110 470, 290 580 L0 580 Z" fill="var(--green)"/>
      <path d="M0 250 C 35 345, 95 475, 265 580 L0 580 Z" fill="var(--magenta)"/>
      <path d="M0 250 C 20 330, 60 430, 140 520 C 70 440, 25 350, 0 300 Z" fill="var(--magenta-light)" opacity="0.5"/>
    </svg>

    <div class="brand">
      <span class="brand-dot"></span>
      <span class="brand-name">BRIGHTWAY MOTOR SALES</span>
    </div>

    <div class="divider"></div>

    <div class="contact">
      <h1 class="contact-name">Daryl Fenn</h1>
      <p class="contact-role">Sales rep</p>
      <p class="contact-address">472 N.Corbin Ave<br>Larkmoor Vale 45990</p>
      <ul class="contact-list">
        <li>
          <svg viewBox="0 0 24 24"><path d="M6.6 10.8a15.1 15.1 0 0 0 6.6 6.6l2.2-2.2a1 1 0 0 1 1-.25 11.4 11.4 0 0 0 3.6.57 1 1 0 0 1 1 1V20a1 1 0 0 1-1 1A17 17 0 0 1 3 4a1 1 0 0 1 1-1h3.5a1 1 0 0 1 1 1c0 1.25.2 2.45.57 3.57a1 1 0 0 1-.25 1z"/></svg>
          513-555-0142
        </li>
        <li>
          <svg viewBox="0 0 24 24"><path d="M7 3h10v5H7zM4 9h16a2 2 0 0 1 2 2v6h-4v4H6v-4H2v-6a2 2 0 0 1 2-2zm4 7v3h8v-3z"/></svg>
          513-555-0178
        </li>
        <li>
          <svg viewBox="0 0 24 24"><path d="M12 2a10 10 0 1 0 5 18.7l-1-1.7A8 8 0 1 1 20 12v1.2a1.8 1.8 0 0 1-3.6 0V7.5h-2v.9A5 5 0 1 0 15 15.6a3.8 3.8 0 0 0 7-2.4V12A10 10 0 0 0 12 2zm0 13a3 3 0 1 1 0-6 3 3 0 0 1 0 6z"/></svg>
          brightwaymotorsales@examplemail.com
        </li>
        <li>
          <svg viewBox="0 0 24 24"><path d="M12 2a10 10 0 1 0 0 20 10 10 0 0 0 0-20zm6.9 9h-3a15 15 0 0 0-1.3-5.6A8 8 0 0 1 18.9 11zM12 4.1c.9 1.2 1.8 3.5 2 6.9h-4c.2-3.4 1.1-5.7 2-6.9zM9.4 5.4A15 15 0 0 0 8.1 11h-3a8 8 0 0 1 4.3-5.6zM5.1 13h3a15 15 0 0 0 1.3 5.6A8 8 0 0 1 5.1 13zm6.9 6.9c-.9-1.2-1.8-3.5-2-6.9h4c-.2 3.4-1.1 5.7-2 6.9zm2.6-1.3a15 15 0 0 0 1.3-5.6h3a8 8 0 0 1-4.3 5.6z"/></svg>
          www.crestvalemotorcars.example
        </li>
      </ul>
    </div>
  </div>
</body>
</html>
```